Insurance Agency website design for Brellow Cover Insurance, LP

Build a website for Brellow Cover Insurance, LP which sells Homeowners, Auto, Renters, Condo, Flood, Disability, Life, Umbrella, and health insurance. We need the coolest insurance agency website out there to get quotes, contact us, or get additional information. Please list the following insurance companies we work with: Varnix, Ostle, Meridale Mutual, Quillor, Dunmarrow, KGZ, and Pellwick.

Make a design similar to https://www.fernagentry.com/

Selling personal insurance policies

```html
<!DOCTYPE html>
<html lang="en">
<head>
<meta charset="UTF-8">
<title>Brellow Cover Insurance, LP</title>
<link href="https://fonts.googleapis.com/css2?family=Poppins:wght@400;500;600&display=swap" rel="stylesheet">
<style>
:root{
  --navy:#173a64;
  --navy-deep:#12325a;
  --green:#14b21f;
  --green-dark:#0a9d15;
  --mint:#d7efd8;
  --paper:#f7f7f7;
  --ink:#4a4a4a;
  --white:#ffffff;
}
*{margin:0;padding:0;box-sizing:border-box}
html,body{width:1200px;height:2283px;overflow:hidden}
body{font-family:'Poppins',sans-serif;color:var(--navy);background:var(--white);position:relative}
.abs{position:absolute}

/* header */
.site-header{position:absolute;left:0;top:0;width:1200px;height:94px;background:var(--white)}
.brand{position:absolute;left:58px;top:22px;display:flex;align-items:center;gap:12px}
.brand-mark{width:46px;height:46px;border-radius:50%;background:var(--green)}
.brand-name{font-size:15px;font-weight:600;line-height:20px;color:var(--navy);width:150px}
.main-nav{position:absolute;left:377px;top:36px;display:flex;gap:46px;font-size:15.5px;color:#555}
.main-nav .active{color:var(--green);font-weight:600}
.contact{position:absolute;top:29px;display:flex;align-items:center;gap:10px}
.contact small{display:block;font-size:12.5px;color:var(--green);line-height:16px}
.contact span{display:block;font-size:13px;color:var(--navy);font-weight:500;line-height:18px}

/* hero */
.hero{position:absolute;left:0;top:94px;width:1200px;height:514px;overflow:hidden}
.hero-left{position:absolute;left:0;top:0;width:742px;height:514px;background:linear-gradient(120deg,#1b4777 0%,#173e6b 55%,#1d4b7c 100%)}
.hero-right{position:absolute;left:742px;top:0;width:458px;height:514px;background:linear-gradient(160deg,#0aa812 0%,#15b21e 60%,#0e9a16 100%)}
.hero h1{position:absolute;left:111px;top:113px;font-size:42px;line-height:52px;font-weight:600;color:var(--white);width:460px}
.hero p{position:absolute;left:111px;top:285px;font-size:15.5px;line-height:28px;color:var(--white);width:420px}
.btn{display:inline-block;background:var(--green);color:var(--white);font-size:13.5px;padding:0 24px;height:38px;line-height:38px;font-weight:500}
.hero .btn{position:absolute;left:111px;top:353px;width:145px}
.hero-photo{position:absolute;left:620px;top:78px;width:464px;height:325px;background:linear-gradient(135deg,#d8d2c7,#b9b4a8 50%,#8e8a80)}
.hero-ring{position:absolute;left:1054px;top:48px;width:118px;height:133px;border-radius:50%;background:rgba(255,255,255,0.18)}
.hero-dots{position:absolute;left:546px;top:316px;width:160px;height:156px;background:rgba(255,255,255,0.08)}

/* partners */
.partners{position:absolute;left:0;top:608px;width:1200px;height:340px;background:var(--paper);border-bottom:1px solid #dcdcdc}
.section-title{font-size:39px;font-weight:500;color:var(--navy);text-align:center}
.section-title em{font-style:normal;color:var(--green)}
.partners .section-title{position:absolute;left:0;top:72px;width:1200px}
.partner-row{position:absolute;left:110px;top:170px;width:980px;height:40px;display:flex;align-items:center;justify-content:space-between}
.partner{font-size:26px;font-weight:500;color:#222;letter-spacing:1px;width:210px;text-align:center}
.partner-sep{width:2px;height:36px;background:#333}
.slider-dots{position:absolute;left:573px;top:242px;display:flex;gap:6px}
.slider-dots i{width:13px;height:13px;border-radius:50%;border:1.5px solid var(--navy);display:block}
.slider-dots i.on{background:var(--green);border-color:var(--green)}

/* coverage */
.coverage{position:absolute;left:0;top:949px;width:1200px;height:594px;background:var(--paper)}
.coverage .section-title{position:absolute;left:0;top:75px;width:1200px}
.cards{position:absolute;left:110px;top:165px;display:flex;gap:24px}
.card{width:227px;height:288px;border:1.5px solid var(--navy);border-radius:14px;background:var(--white);padding:22px 22px 0}
.card-icon{width:68px;height:68px;border-radius:10px;background:var(--green);display:flex;align-items:center;justify-content:center}
.card h3{font-size:19px;font-weight:500;margin-top:16px;color:var(--navy)}
.card p{font-size:13px;line-height:21.5px;color:var(--ink);margin-top:12px}
.card .more{display:inline-block;margin-top:16px;background:#e9e9e9;color:#333;font-size:13.5px;padding:0 17px;height:37px;line-height:37px}
.explore{position:absolute;left:0;top:492px;width:1200px;text-align:center;font-size:15.5px;color:#555}
.explore a{color:var(--navy);font-weight:500;text-decoration:underline}

/* about */
.about{position:absolute;left:0;top:1543px;width:1200px;height:575px;background:linear-gradient(135deg,#d6eed7,#e0f3e0 60%,#d3ecd4)}
.about-photo-a{position:absolute;left:111px;top:87px;width:358px;height:304px;background:linear-gradient(135deg,#c9b49a,#8a6d52 55%,#4d4034)}
.about-frame{position:absolute;left:365px;top:267px;width:207px;height:235px;background:#c9eccb;border-radius:8px}
.about-photo-b{position:absolute;left:378px;top:279px;width:181px;height:209px;background:linear-gradient(180deg,#efe8e2,#d9c7b7 55%,#a57b5d)}
.about h2{position:absolute;left:602px;top:114px;font-size:39px;font-weight:500;color:var(--navy)}
.about h2 em{font-style:normal;color:var(--green)}
.about p{position:absolute;left:602px;top:176px;width:495px;font-size:15.5px;line-height:27.5px;color:#555}
.about .btn{position:absolute;left:602px;top:419px;width:145px;height:37px;line-height:37px;padding:0 25px}

/* footer */
.site-footer{position:absolute;left:0;top:2118px;width:1200px;height:165px;background:var(--navy-deep)}
.footer-brand{position:absolute;left:109px;top:48px;display:flex;align-items:center;gap:18px}
.footer-brand .brand-mark{width:78px;height:78px;background:var(--white)}
.footer-brand .brand-name{font-size:23px;line-height:30px;color:var(--white);width:300px}
.footer-nav{position:absolute;right:111px;top:54px;display:flex;gap:44px;font-size:15.5px;color:var(--white);font-weight:500}
.footer-rule{position:absolute;left:647px;top:86px;width:442px;height:1px;background:rgba(255,255,255,0.6)}
.copyright{position:absolute;right:111px;top:100px;font-size:13px;color:var(--white)}
</style>
</head>
<body>

<header class="site-header">
  <div class="brand"><div class="brand-mark"></div><div class="brand-name">Brellow Cover Insurance LP</div></div>
  <nav class="main-nav"><span class="active">Home</span><span>About Us</span><span>Get a Quote</span></nav>
  <div class="contact" style="left:753px">
    <svg width="26" height="26" viewBox="0 0 24 24"><path fill="#111" d="M6.6 10.8a15.1 15.1 0 0 0 6.6 6.6l2.2-2.2c.3-.3.7-.4 1-.2 1.1.4 2.3.6 3.6.6.6 0 1 .4 1 1V20c0 .6-.4 1-1 1A17 17 0 0 1 3 4c0-.6.4-1 1-1h3.5c.6 0 1 .4 1 1 0 1.2.2 2.4.6 3.6.1.3 0 .7-.2 1l-2.3 2.2z"/></svg>
    <div><small>Call Us</small><span>(555) 318-2740</span></div>
  </div>
  <div class="contact" style="left:890px">
    <svg width="28" height="22" viewBox="0 0 28 22"><rect x="0" y="0" width="28" height="22" rx="2" fill="#111"/><path d="M1 2l13 10L27 2" stroke="#fff" stroke-width="2" fill="none"/></svg>
    <div><small>Mail Us</small><span>hello@brellowcover.com</span></div>
  </div>
</header>

<section class="hero">
  <div class="hero-left"></div>
  <div class="hero-right"></div>
  <div class="hero-dots" role="img" aria-label="Decorative dot grid"></div>
  <div class="hero-ring" role="img" aria-label="Decorative striped circle"></div>
  <h1>Secure Your Future with Brellow Cover Insurance</h1>
  <p>Brellow Cover Insurance is a full-service, independent insurance agency with over three decades</p>
  <a class="btn">Get Started &rarr;</a>
  <div class="hero-photo" role="img" aria-label="Photo of a smiling family sitting in their living room under a cardboard roof"></div>
</section>

<section class="partners">
  <h2 class="section-title">Our <em>Partner</em></h2>
  <div class="partner-row">
    <span class="partner">VARNIX</span><span class="partner-sep"></span>
    <span class="partner">Meridale Mutual</span><span class="partner-sep"></span>
    <span class="partner">Quillor</span><span class="partner-sep"></span>
    <span class="partner">PELLWICK</span>
  </div>
  <div class="slider-dots"><i></i><i class="on"></i><i></i></div>
</section>

<section class="coverage">
  <h2 class="section-title">Insurance <em>Coverage</em></h2>
  <div class="cards">
    <div class="card">
      <div class="card-icon"><svg width="40" height="36" viewBox="0 0 40 36"><path d="M20 2L2 18h6v16h9V24h6v10h9V18h6z" fill="#fff"/></svg></div>
      <h3>Homeowners</h3>
      <p>Lorem ipsum dolor sit amet, consectetur adipiscing elit, sed do</p>
      <a class="more">Read More &rarr;</a>
    </div>
    <div class="card">
      <div class="card-icon"><svg width="34" height="40" viewBox="0 0 34 40"><circle cx="17" cy="5" r="4" fill="#fff"/><path d="M15 12v12h10l5 10M12 18a10 10 0 1 0 13 14" stroke="#fff" stroke-width="3.5" fill="none" stroke-linecap="round"/></svg></div>
      <h3>Disability</h3>
      <p>Lorem ipsum dolor sit amet, consectetur adipiscing elit, sed do</p>
      <a class="more">Read More &rarr;</a>
    </div>
    <div class="card">
      <div class="card-icon"><svg width="40" height="38" viewBox="0 0 40 38"><path d="M20 4L4 18h5v16h22V18h5z" fill="none" stroke="#fff" stroke-width="3"/><rect x="16" y="24" width="8" height="10" fill="#fff"/></svg></div>
      <h3>Renters</h3>
      <p>Lorem ipsum dolor sit amet, consectetur adipiscing elit, sed do</p>
      <a class="more">Read More &rarr;</a>
    </div>
    <div class="card">
      <div class="card-icon"><svg width="44" height="40" viewBox="0 0 44 40"><path d="M22 38S3 26 3 13a9.5 9.5 0 0 1 19-1 9.5 9.5 0 0 1 19 1c0 13-19 25-19 25z" fill="#fff"/><path d="M22 15v12M16 21h12" stroke="#14b21f" stroke-width="4"/></svg></div>
      <h3>Health Insurance</h3>
      <p>Lorem ipsum dolor sit amet, consectetur adipiscing elit, sed do</p>
      <a class="more">Read More &rarr;</a>
    </div>
  </div>
  <p class="explore">Do You Want To explore more services just <a>Click Here</a></p>
</section>

<section class="about">
  <div class="about-photo-a" role="img" aria-label="Photo of a couple reviewing documents with an insurance agent"></div>
  <div class="about-frame"></div>
  <div class="about-photo-b" role="img" aria-label="Photo of hands sheltering a model house"></div>
  <h2>About <em>Us</em></h2>
  <p>Brellow Cover Insurance is a full-service, independent insurance agency with over three decades of experience in delivering comprehensive insurance solutions to individuals. We proudly offer a diverse portfolio of products from more than 20 of the most reputable and financially secure companies in the industry. Our dedicated team of over 50 skilled professionals is committed to customizing these products and services to meet the unique needs of each client.</p>
  <a class="btn">Learn More &rarr;</a>
</section>

<footer class="site-footer">
  <div class="footer-brand"><div class="brand-mark"></div><div class="brand-name">Brellow Cover Insurance LP</div></div>
  <nav class="footer-nav"><span>Home</span><span>About Us</span><span>Get a Quote</span></nav>
  <div class="footer-rule"></div>
  <p class="copyright">Copyright &copy; 2025 Brellow Cover Insurance LP. All rights reserved.</p>
</footer>

</body>
</html>
```